Tavenhurst Falcons FC Website

We are looking to develop a new website for Tavenhurst FC. Tavenhurst FC has now joined with Tavenhurst Falcons FC and we are looking at a website that can work for both clubs. Tavenhurst FC play in a local park football competition while tavenhurst Falcons are a Semi Professional team that plays in the Ostral Premier Series Competition. What we are after is two separate website off the one platform. I have attached both team logos for you to visualise. Also you can look at the existing tavenhurst website www.tavenhurstfc.net.au. We are looking for a huge improvement in the website and it will be imperative we have links to sponsors and the sponsors can get regular visuals. Weare looking to move this club forward and have a very professional website that can communicate clearly with the community.

Hi All,

Please remember that the website is to represent two clubs;
1. Tavenhurst Falcons FC (Competes in Semi Professional League)
2. Tavenhurst FC (Compete in KPWLT League which is a lower level)

Further to this the Tavenhurst Falcons FC page will require a player profile page which will show photos of each player and a little bio on each.

Thanks

Reason: Would like to spend more time review existing and new designs

```html
<!DOCTYPE html>
<html lang="en">
<head>
<meta charset="utf-8">
<title>Tavenhurst Falcons FC</title>
<link href="https://fonts.googleapis.com/css2?family=Crimson+Text:wght@400;600;700&family=Arimo:wght@400;700&display=swap" rel="stylesheet">
<style>
:root{
  --red:#d0000a;
  --ink:#222;
  --muted:#555;
  --grey-text:#777;
  --page:#f1f0ee;
  --dark:#3a3a3a;
  --line:#d8d6d2;
}
*{box-sizing:border-box;margin:0;padding:0}
html,body{width:875px;height:1200px;overflow:hidden}
body{position:relative;background:var(--page);font-family:"Crimson Text",Georgia,serif;color:var(--ink)}
.abs{position:absolute}
.header{left:0;top:0;width:875px;height:110px;background:linear-gradient(#fff,#f3f3f3)}
.brand-mark{left:120px;top:16px;width:70px;height:70px;border-radius:50%;background:var(--red)}
.site-title{left:219px;top:36px;font-size:17px;font-weight:700;color:#333;line-height:20px}
.site-tag{left:219px;top:56px;font-size:12.5px;color:#888;line-height:15px}
.social{top:30px;width:11px;height:11px;border-radius:50%;background:var(--red)}
.register{left:652px;top:52px;width:105px;height:23px;background:var(--dark);border:2px solid #fff;outline:1px solid var(--dark);color:#fff;font:9.5px Arimo,Arial,sans-serif;text-align:center;line-height:19px;letter-spacing:.2px}
.nav{left:0;top:110px;width:875px;height:24px;background:var(--red)}
.nav-item{top:0;height:24px;color:#fff;font:9px Arimo,Arial,sans-serif;line-height:24px;text-align:center;border-right:1px solid #e8454b;white-space:nowrap}
.nav-item svg{vertical-align:middle;margin-left:5px}
.nav-item.active{background:var(--dark)}
.dropdown{left:591px;top:134px;width:97px;padding-top:5px;background:#f5f5f5;box-shadow:0 2px 3px rgba(0,0,0,.15);z-index:3}
.dropdown div{height:20.5px;line-height:20px;text-align:center;font:9px Arimo,Arial,sans-serif;color:var(--red);border-bottom:1px solid #e2e2e2}
.dropdown div:last-child{border-bottom:0}
.hero{left:0;top:134px;width:875px;height:320px;background:linear-gradient(100deg,#8a8864 0%,#6d6a4c 25%,#3c3a30 45%,#4a4a3c 58%,#3b6a36 75%,#2f6b30 88%,#24502a 100%)}
.hero-arrow{top:280px;width:31px;height:30px;background:#333}
.hero-caption{left:345px;top:230px;width:185px;height:27px;background:rgba(40,40,40,.85);color:#fff;font-size:16px;text-align:center;line-height:27px}
.card{top:374px;width:192px;height:239px;background:#fff;border-top:5px solid var(--red);text-align:center;box-shadow:0 8px 8px -6px rgba(0,0,0,.25)}
.card h2{font-size:15px;font-weight:600;margin-top:8px;color:#333;line-height:20px}
.card .photo{width:160px;height:88px;margin:9px auto 0;border:3px solid #eee}
.card p{font-size:9px;line-height:12px;color:var(--muted);margin:12px 14px 0}
.btn{display:inline-block;background:var(--red);color:#fff;border:2px solid #fff;outline:1px solid var(--red);font-size:11px;line-height:16px;padding:1px 8px}
.card .btn{margin-top:12px}
.section-title{top:645px;font-size:17px;font-weight:600;color:#333;line-height:22px}
.news{left:118px;width:375px;height:100px}
.news .thumb{left:0;top:0;width:80px;height:80px;border:3px solid #fff;box-shadow:0 0 2px rgba(0,0,0,.25)}
.news .date{left:98px;top:1px;font-size:11px;color:#555}
.news p{left:98px;top:20px;width:275px;font-size:9px;line-height:12px;color:var(--muted)}
.news .more{left:98px;top:71px;font-size:8px;color:var(--red);text-decoration:underline}
.rule{left:118px;width:375px;height:1px;background:var(--line)}
.divider{left:517px;top:650px;width:1px;height:382px;background:var(--line)}
.fix{width:98px;height:98px;background:#fff;box-shadow:0 0 2px rgba(0,0,0,.2);padding:6px}
.fix div{width:100%;height:100%}
.fix-label{width:98px;text-align:center;font-size:10.5px;color:#333}
.footer{left:0;top:1054px;width:875px;height:146px;background:#fafafa;border-top:1px solid var(--line)}
.foot-links{left:118px;top:1073px;font:8px Arimo,Arial,sans-serif;color:var(--grey-text)}
.foot-links span.sep{margin:0 5px}
.foot-links .on{color:var(--red)}
.foot-brand{left:152px;top:1130px;font-size:11px;font-weight:700;color:var(--red)}
.foot-dot{left:120px;top:1124px;width:26px;height:26px;border-radius:50%;background:var(--red)}
.copy{left:118px;top:1168px;font:8px Arimo,Arial,sans-serif;color:var(--grey-text)}
.copy u{margin-left:6px}
.fsoc{top:1170px;width:9px;height:9px;border-radius:50%;background:var(--red)}
.foot-list{top:1072px;list-style:none;font:8px Arimo,Arial,sans-serif;color:#444}
.foot-list li{height:19.2px;padding-left:8px;position:relative}
.foot-list li::before{content:"";position:absolute;left:0;top:3px;width:3px;height:3px;background:var(--red)}
</style>
</head>
<body>
<header class="abs header"></header>
<div class="abs brand-mark"></div>
<div class="abs site-title">Tavenhurst Falcons FC</div>
<div class="abs site-tag">Welcome to Our Official Website</div>
<div class="abs social" style="left:695px"></div>
<div class="abs social" style="left:720px"></div>
<div class="abs social" style="left:745px"></div>
<div class="abs register">REGISTER ONLINE</div>

<nav class="abs nav">
  <div class="abs nav-item" style="left:128px;width:67px">HOME</div>
  <div class="abs nav-item" style="left:195px;width:67px">NEWS</div>
  <div class="abs nav-item" style="left:262px;width:132px">FIXTURE &amp; RESULTS<svg width="7" height="5"><path d="M0.5 0.5 L3.5 3.5 L6.5 0.5" stroke="#fff" stroke-width="1.5" fill="none"/></svg></div>
  <div class="abs nav-item" style="left:394px;width:108px">PHOTO GALLERY</div>
  <div class="abs nav-item" style="left:502px;width:89px">SPONSOR</div>
  <div class="abs nav-item active" style="left:591px;width:75px">CLUB<svg width="7" height="5"><path d="M0.5 0.5 L3.5 3.5 L6.5 0.5" stroke="#fff" stroke-width="1.5" fill="none"/></svg></div>
  <div class="abs nav-item" style="left:666px;width:80px;border:0">CONTACT US</div>
</nav>
<div class="abs dropdown">
  <div>History</div><div>Management</div><div>Awards</div><div>Registration</div>
</div>

<section class="abs hero" role="img" aria-label="Action photo of a striker kicking the ball past a diving goalkeeper on a grass pitch"></section>
<div class="abs hero-caption">The Game Is About <b>Glory</b></div>
<div class="abs hero-arrow" style="left:35px"><svg width="31" height="30"><path d="M18 8 L11 15 L18 22" stroke="#fff" stroke-width="2" fill="none"/></svg></div>
<div class="abs hero-arrow" style="left:803px"><svg width="31" height="30"><path d="M13 8 L20 15 L13 22" stroke="#fff" stroke-width="2" fill="none"/></svg></div>

<article class="abs card" style="left:118px">
  <h2>News Headlines</h2>
  <div class="photo" role="img" aria-label="Junior players sitting on the grass with their coach" style="background:linear-gradient(#8a9a78 0%,#6e9050 35%,#4f7a38 100%)"></div>
  <p>Lorem ipsum dolor sit amet, consectetur adipisicing elit, sed do eiusmod tempor incididunt ...</p>
  <span class="btn">more</span>
</article>
<article class="abs card" style="left:342px">
  <h2>Our Mission</h2>
  <div class="photo" role="img" aria-label="Club trophy shield in a display cabinet" style="background:radial-gradient(circle at 50% 45%,#b09070 0%,#7a3a2a 45%,#4a2018 100%)"></div>
  <p>Lorem ipsum dolor sit amet, consectetur adipisicing elit, sed do eiusmod tempor incididunt ut labore et ...</p>
  <span class="btn">more</span>
</article>
<article class="abs card" style="left:566px">
  <h2>Sponsors</h2>
  <div class="photo" role="img" aria-label="Sponsors standing in a row at a club function" style="background:linear-gradient(#a09a94 0%,#5a5450 55%,#7a3a34 80%,#3a3432 100%)"></div>
  <p>Lorem ipsum dolor sit amet, consectetur adipisicing elit, sed do eiusmod tempor incididunt ut ...</p>
  <span class="btn">more</span>
</article>

<h2 class="abs section-title" style="left:118px">Latest News Updates !</h2>
<div class="abs news" style="top:686px">
  <div class="abs thumb" role="img" aria-label="Officials signing an agreement" style="background:linear-gradient(#c0a890,#8a5040 55%,#5a3028)"></div>
  <div class="abs date">18 Mar</div>
  <p class="abs">Lorem ipsum dolor sit amet, consectetur adipisicing elit, sed do eiusmod tempor incididunt ut labore et dolore magna aliqua. Ut enim ad minim veniam, quis nostrud exercitation ullamco ...</p>
  <div class="abs more">MORE INFO</div>
</div>
<div class="abs rule" style="top:781px"></div>
<div class="abs news" style="top:795px">
  <div class="abs thumb" role="img" aria-label="Club members posing outdoors" style="background:linear-gradient(#9ab0c0,#6a5a48 50%,#4a6a34)"></div>
  <div class="abs date">5 Mar</div>
  <p class="abs">Lorem ipsum dolor sit amet, consectetur adipisicing elit, sed do eiusmod tempor incididunt ut labore et dolore magna aliqua. Ut enim ad minim veniam, quis nostrud exercitation ullamco ...</p>
  <div class="abs more">MORE INFO</div>
</div>
<div class="abs rule" style="top:891px"></div>
<div class="abs news" style="top:904px">
  <div class="abs thumb" role="img" aria-label="Award presentation at a club night" style="background:linear-gradient(#b08a68,#5a4038 55%,#2e2a2a)"></div>
  <div class="abs date">22 Feb</div>
  <p class="abs">Lorem ipsum dolor sit amet, consectetur adipisicing elit, sed do eiusmod tempor incididunt ut labore et dolore magna aliqua. Ut enim ad minim veniam, quis nostrud exercitation ullamco ...</p>
  <div class="abs more">MORE INFO</div>
</div>
<span class="abs btn" style="left:118px;top:1010px">read more</span>

<div class="abs divider"></div>

<h2 class="abs section-title" style="left:541px">Fixture &amp; Results</h2>
<div class="abs fix" style="left:541px;top:686px"><div role="img" aria-label="Player in red kicking the ball" style="background:linear-gradient(#b0aea6 0%,#8a9a80 40%,#4f8a3c 100%)"></div></div>
<div class="abs fix" style="left:660px;top:686px"><div role="img" aria-label="Goalkeeper in yellow clearing the ball" style="background:linear-gradient(#7aa058,#4f8a38 60%,#3f7a30)"></div></div>
<div class="abs fix-label" style="left:541px;top:791px">Premier League</div>
<div class="abs fix-label" style="left:660px;top:791px">Super League</div>
<div class="abs fix" style="left:541px;top:826px"><div role="img" aria-label="Player celebrating a goal" style="background:linear-gradient(#6aaa44,#4a8a30 60%,#3a7a28)"></div></div>
<div class="abs fix" style="left:660px;top:826px"><div role="img" aria-label="Two players contesting the ball" style="background:linear-gradient(#2e4a28,#4a7a38 55%,#5a9a44)"></div></div>
<div class="abs fix-label" style="left:541px;top:931px">Under 16 / 2</div>
<div class="abs fix-label" style="left:660px;top:931px">Under 17 / 1</div>
<span class="abs btn" style="left:541px;top:978px;padding:1px 14px">more</span>

<footer class="abs footer"></footer>
<div class="abs foot-links"><span class="on">Home</span><span class="sep">|</span>News<span class="sep">|</span>Fixture &amp; Results<span class="sep">|</span>Photo Gallery<span class="sep">|</span>Sponsor<span class="sep">|</span>Club<span class="sep">|</span>Contact Us</div>
<div class="abs foot-dot"></div>
<div class="abs foot-brand">Tavenhurst FC</div>
<div class="abs copy">&copy; 2014 &nbsp;| <u>Privacy Policy</u></div>
<div class="abs fsoc" style="left:237px"></div>
<div class="abs fsoc" style="left:255px"></div>
<div class="abs fsoc" style="left:273px"></div>
<ul class="abs foot-list" style="left:562px"><li>News</li><li>Tournaments</li><li>Teams</li><li>Training</li><li>Equipment</li><li>Recruiting</li></ul>
<ul class="abs foot-list" style="left:684px"><li>Recruiting Camps</li><li>Services</li><li>Calendar</li><li>Clinics</li><li>Photo Album</li><li>Our Sponsors</li></ul>
</body>
</html>
```